Coastline Premier Retreats Business Card Design

Design a business card for Coastline Premier Retreats. Look at the website for colors and reference. Card should have logo, name, title, office number, mobile number, email, URL and a tagline like, "Luxury Hotel & Resort Email Marketing" (This might change).

https://www.coastlinepremierretreats.example

The rest I will leave up to your imagination.

Contact Information for Business Card

Logo, name, title, office number, mobile number, email, URL and a tagline like, "Luxury Hotel & Resort Email Marketing" (This might change).

```html
<!DOCTYPE html>
<html lang="en">
<head>
<meta charset="utf-8">
<title>Coastline Premier Retreats – Business Card</title>
<link rel="stylesheet" href="https://fonts.googleapis.com/css2?family=Montserrat:wght@600;700;800&family=Open+Sans:wght@400;600&display=swap">
<style>
  :root {
    --bg: #17171a;
    --card: #1f1f23;
    --card-emboss: #29292e;
    --orange: #f47920;
    --white: #ffffff;
    --muted: #e9e9ea;
  }
  * { box-sizing: border-box; margin: 0; padding: 0; }
  html, body { width: 1200px; height: 780px; overflow: hidden; background: var(--bg); }
  .canvas { position: relative; width: 1200px; height: 780px; }

  .card {
    position: absolute;
    top: 235px;
    width: 540px;
    height: 310px;
    background: var(--card);
    border-radius: 20px;
    border-bottom: 3px solid var(--orange);
    border-left: 2px solid var(--orange);
    overflow: hidden;
  }
  .card--back { left: 30px; }
  .card--front { left: 630px; }

  /* back side */
  .back-mark {
    position: absolute; inset: 0;
    display: flex; align-items: center; justify-content: center; gap: 14px;
  }
  .back-mark__square { width: 22px; height: 22px; background: var(--card-emboss); }
  .back-mark__name {
    font-family: "Montserrat", sans-serif; font-weight: 800;
    font-size: 28px; line-height: 1.05; letter-spacing: 1px;
    text-transform: uppercase; color: var(--card-emboss);
  }

  /* front side */
  .brand {
    position: absolute; left: 34px; top: 112px; width: 200px;
    display: flex; align-items: center; gap: 10px;
  }
  .brand__square { flex: none; width: 14px; height: 14px; background: var(--orange); }
  .brand__name {
    font-family: "Montserrat", sans-serif; font-weight: 800;
    font-size: 19px; line-height: 1.1; text-transform: uppercase;
    color: var(--white); letter-spacing: 0.5px;
  }
  .divider {
    position: absolute; left: 250px; top: 58px; width: 2px; height: 150px;
    background: var(--white);
  }
  .person { position: absolute; left: 272px; top: 46px; }
  .person__name {
    font-family: "Montserrat", sans-serif; font-weight: 800; font-size: 23px;
    color: var(--white); line-height: 1.1;
  }
  .person__first { color: var(--orange); }
  .person__title {
    font-family: "Open Sans", sans-serif; font-weight: 600; font-size: 13px;
    color: var(--muted); margin-top: 3px;
  }
  .contacts { list-style: none; margin-top: 14px; }
  .contacts li {
    display: flex; align-items: center; gap: 9px;
    font-family: "Open Sans", sans-serif; font-size: 12.5px; color: var(--muted);
    line-height: 21px;
  }
  .contacts svg { width: 13px; height: 13px; flex: none; }
  .tagline {
    position: absolute; left: 130px; bottom: 62px;
    font-family: "Open Sans", sans-serif; font-size: 13px; color: var(--orange);
    letter-spacing: 0.3px;
  }
  .bands { position: absolute; left: 0; bottom: 0; width: 540px; height: 90px; }
</style>
</head>
<body>
<main class="canvas">

  <section class="card card--back" aria-label="Card back">
    <div class="back-mark">
      <span class="back-mark__square"></span>
      <span class="back-mark__name">Coastline<br>Premier Retreats</span>
    </div>
  </section>

  <section class="card card--front" aria-label="Card front">
    <div class="brand">
      <span class="brand__square"></span>
      <span class="brand__name">Coastline Premier Retreats</span>
    </div>

    <div class="divider"></div>

    <div class="person">
      <h1 class="person__name"><span class="person__first">Daria</span> Kovacek</h1>
      <p class="person__title">Managing Director</p>
      <ul class="contacts">
        <li>
          <svg viewBox="0 0 24 24" aria-hidden="true"><path fill="#f47920" d="M6.6 10.8a15.1 15.1 0 0 0 6.6 6.6l2.2-2.2a1 1 0 0 1 1-.25 11.4 11.4 0 0 0 3.6.57 1 1 0 0 1 1 1V20a1 1 0 0 1-1 1A17 17 0 0 1 3 4a1 1 0 0 1 1-1h3.5a1 1 0 0 1 1 1c0 1.25.2 2.45.57 3.6a1 1 0 0 1-.25 1z"/></svg>
          (555) 302-4816
        </li>
        <li>
          <svg viewBox="0 0 24 24" aria-hidden="true"><rect x="6" y="2" width="12" height="20" rx="2" fill="none" stroke="#f47920" stroke-width="2"/><circle cx="12" cy="18" r="1.2" fill="#f47920"/></svg>
          (555) 410-7720
        </li>
        <li>
          <svg viewBox="0 0 24 24" aria-hidden="true"><circle cx="12" cy="12" r="9" fill="none" stroke="#f47920" stroke-width="2"/><path d="M3 12h18M12 3c3 3 3 15 0 18M12 3c-3 3-3 15 0 18" fill="none" stroke="#f47920" stroke-width="1.6"/></svg>
          www.coastlinepremierretreats.example
        </li>
        <li>
          <svg viewBox="0 0 24 24" aria-hidden="true"><rect x="2" y="5" width="20" height="14" rx="2" fill="#f47920"/><path d="M3 6l9 7 9-7" fill="none" stroke="#1f1f23" stroke-width="1.8"/></svg>
          info@coastlinepremierretreats.example
        </li>
      </ul>
    </div>

    <p class="tagline">Luxury Hotel &amp; Resort Email Marketing</p>

    <svg class="bands" viewBox="0 0 540 90" preserveAspectRatio="none" aria-hidden="true">
      <polygon points="0,90 0,70 300,60 330,48 300,90" fill="var(--orange)"/>
      <polygon points="300,60 330,48 540,20 540,58 350,64" fill="var(--white)"/>
    </svg>
  </section>

</main>
</body>
</html>
```